New business card/stationary for a consulting company

I am looking for a clean and very professional looking business card for my consulting company as well as corresponding stationary. I am uploading our logo. I like simple and powerful for the feel. No graphics but I am open on everything else. Below is my contact information but would like the final to be in a version I can add my employees information into and print. Thank you.

Daniel Whitcombe
dan@ferncliffadvisory.com
2870 North 9th Avenue, Summit Floor, Elm Ridge, Illinois 60531
www.ferncliffadvisory.com

Industry/Entity Type

Consulting

Contact Information for Business Card

Daniel Whitcombe
dan@ferncliffadvisory.com
www.ferncliffadvisory.com

Font styles to use
Serif
Sans Serif

Requirements
Must have
• Our logo and the business card details.
Nice to have
• our website www.ferncliffadvisory.com

```html
<!DOCTYPE html>
<html lang="en">
<head>
<meta charset="utf-8">
<title>Ferncliff Advisory — Business Card</title>
<link rel="stylesheet" href="https://fonts.googleapis.com/css2?family=Arimo:wght@400;700&display=swap">
<style>
  :root {
    --navy: #0b0b82;
    --navy-deep: #06066e;
    --paper: #f4f4f4;
    --ink-grey: #555555;
    --backdrop: #e6e3dd;
    --white: #ffffff;
  }
  * { box-sizing: border-box; margin: 0; padding: 0; }
  html, body {
    width: 1200px;
    height: 886px;
    overflow: hidden;
    background: var(--backdrop);
    font-family: "Arimo", Arial, sans-serif;
  }
  .canvas {
    position: relative;
    width: 1200px;
    height: 886px;
  }

  /* Front of card */
  .card-front {
    position: absolute;
    left: 150px;
    top: 145px;
    width: 340px;
    height: 595px;
    background: var(--paper);
    box-shadow: 0 6px 18px rgba(0,0,0,0.18);
    overflow: hidden;
  }
  .front-band {
    height: 118px;
    background: var(--navy);
    display: flex;
    align-items: center;
    justify-content: center;
  }
  .front-band-gap { height: 7px; background: var(--paper); }
  .front-band-rule { height: 9px; background: var(--navy); }
  .brand-name {
    color: var(--white);
    font-weight: 400;
    font-size: 30px;
    letter-spacing: 1px;
  }
  .contact {
    margin-top: 130px;
    text-align: center;
    line-height: 1.35;
  }
  .contact-name {
    color: var(--navy);
    font-weight: 700;
    font-size: 19px;
    font-variant: small-caps;
    letter-spacing: 1px;
  }
  .contact-email,
  .contact-address {
    color: var(--ink-grey);
    font-size: 13px;
  }
  .contact-email { margin-bottom: 6px; }
  .contact-web {
    color: var(--ink-grey);
    font-weight: 700;
    font-size: 13px;
    letter-spacing: 0.5px;
  }

  /* Back of card */
  .card-back {
    position: absolute;
    left: 560px;
    top: 272px;
    width: 595px;
    height: 340px;
    background: linear-gradient(135deg, var(--navy) 0%, var(--navy-deep) 100%);
    box-shadow: 0 6px 18px rgba(0,0,0,0.22);
    display: flex;
    flex-direction: column;
    align-items: center;
    justify-content: center;
    gap: 26px;
  }
  .back-mark {
    width: 56px;
    height: 56px;
    background: var(--white);
  }
  .back-name {
    color: var(--white);
    font-weight: 400;
    font-size: 34px;
    letter-spacing: 3px;
    text-transform: uppercase;
  }
</style>
</head>
<body>
<main class="canvas">
  <section class="card-front" aria-label="Business card front">
    <div class="front-band">
      <span class="brand-name">Ferncliff Advisory</span>
    </div>
    <div class="front-band-gap"></div>
    <div class="front-band-rule"></div>
    <div class="contact">
      <p class="contact-name">Daniel Whitcombe</p>
      <p class="contact-email">dan@ferncliffadvisory.com</p>
      <p class="contact-address">2870 North 9th Avenue</p>
      <p class="contact-address">Summit Floor, Elm Ridge, Illinois 60531</p>
      <p class="contact-web">WWW.FERNCLIFFADVISORY.COM</p>
    </div>
  </section>

  <section class="card-back" aria-label="Business card back">
    <div class="back-mark"></div>
    <p class="back-name">Ferncliff Advisory</p>
  </section>
</main>
</body>
</html>
```